The design should look similar to the uploaded example to accommodate the information needed for a business card template. I would like to see the colors orange and charcoal grey incorporated along with the logo.The following should be on the back of the card SPECIALIZING IN NEW AND USED TIRES & WHEELS FOR:- Loaders- Skid Steers- Telehandlers- Boom Lifts- Forklifs and moreELIMINATING DOWNTIMEWheel Exchange Program for New & Used Foam Filled and Solid Rubber TiresSPECIALTY SERVICES- Foam Filling Tires- Largest Tire Press in SE- ONSITE Forklift Tire Press- Boom Truck Services - Rubber Tracks

Target Market(s)

New and Existing Customers

Industry/Entity Type

Business

Contact Information for Business Card

NAMEHEAVY DUTY TIRE, LLC8470 Belvedere RoadWest Palm Beach, FL 33411P: 844-HD-TIRESF: 561-431-6469C:E: W: WWW.GRANITERIMSUPPLY-EXAMPLE.COM

Font styles to use
Sans Serif

Colors
f37122
333333

Requirements
Must have
• The logo and the information indicated for the backside of the card
Nice to have
• Keep the orange and charcoal grey colors

```html
<!DOCTYPE html>
<html lang="en">
<head>
<meta charset="utf-8">
<title>Granite Rim Supply – Business Card</title>
<link rel="stylesheet" href="https://fonts.googleapis.com/css2?family=Source+Sans+3:wght@400;600;700&display=swap">
<style>
  :root {
    --stage: #6c7b9b;
    --card-white: #ffffff;
    --charcoal: #3b4944;
    --orange: #f58634;
    --ink: #222222;
    --on-dark: #ffffff;
  }
  * { box-sizing: border-box; margin: 0; padding: 0; }
  html, body { width: 1200px; height: 900px; overflow: hidden; }
  body {
    background: var(--stage);
    font-family: "Source Sans 3", "Segoe UI", sans-serif;
    position: relative;
  }
  .card {
    position: absolute;
    top: 200px;
    width: 310px;
    height: 502px;
  }
  .card-front {
    left: 265px;
    background: var(--card-white);
    border-radius: 56px 0 56px 0;
    color: var(--ink);
  }
  .card-back {
    left: 641px;
    width: 309px;
    background: var(--charcoal);
    border-radius: 0 56px 0 56px;
    color: var(--on-dark);
  }
  .brand-mark {
    position: absolute;
    left: 126px;
    top: 25px;
    width: 130px;
    height: 150px;
    display: flex;
    flex-direction: column;
    align-items: center;
    justify-content: center;
    gap: 10px;
  }
  .brand-mark .brand-dot {
    width: 64px; height: 64px;
    border-radius: 50%;
    background: var(--orange);
  }
  .brand-mark .brand-name {
    font-size: 19px;
    font-weight: 700;
    color: var(--charcoal);
    white-space: nowrap;
  }
  .holder-name {
    position: absolute;
    left: 24px; top: 247px;
    font-size: 20.5px;
    font-weight: 600;
    color: var(--orange);
  }
  .company {
    position: absolute;
    left: 24px; top: 289px;
    font-size: 16.5px;
    font-weight: 600;
    color: var(--orange);
    letter-spacing: 0.3px;
  }
  .address {
    position: absolute;
    left: 24px; top: 314px;
    font-size: 15px;
    line-height: 21px;
    font-style: normal;
  }
  .contact-list {
    position: absolute;
    left: 24px; top: 378px;
    list-style: none;
    font-size: 15px;
    line-height: 21px;
  }
  .contact-list li { display: flex; align-items: center; gap: 10px; white-space: nowrap; }
  .contact-list svg { width: 11px; height: 11px; fill: var(--orange); flex: none; }

  .section-title {
    position: absolute;
    left: 35px;
    font-size: 18px;
    font-weight: 600;
    color: var(--orange);
    line-height: 21px;
    letter-spacing: 0.2px;
    white-space: nowrap;
  }
  .bullet-list {
    position: absolute;
    list-style: none;
    font-size: 14.8px;
    font-weight: 600;
    line-height: 20.7px;
    white-space: nowrap;
  }
  .bullet-list li { position: relative; padding-left: 14px; }
  .bullet-list li::before {
    content: "";
    position: absolute;
    left: 0; top: 8px;
    width: 6px; height: 6px;
    border-radius: 50%;
    background: var(--orange);
  }
  .services-title { top: 33px; }
  .services-list { left: 36px; top: 63px; }
  .downtime-title { top: 214px; }
  .downtime-text {
    position: absolute;
    left: 35px; top: 234px;
    font-size: 14.8px;
    font-weight: 600;
    line-height: 19px;
    white-space: nowrap;
  }
  .specialize-title { top: 328px; }
  .equipment-list { left: 34px; top: 380px; }
  .equipment-list li { padding-left: 11px; }
</style>
</head>
<body>
  <section class="card card-front" aria-label="Card front">
    <div class="brand-mark">
      <span class="brand-dot"></span>
      <span class="brand-name">Granite Rim</span>
    </div>
    <h1 class="holder-name">Marcus Delane</h1>
    <h2 class="company">GRANITE RIM SUPPLY, LLC</h2>
    <address class="address">5126 Marston Lane<br>Harlow Springs, FL 33092</address>
    <ul class="contact-list">
      <li><svg viewBox="0 0 12 12"><path d="M2.5 1l2 2.2-1 1.3a7 7 0 0 0 4 4l1.3-1L11 9.5 9.6 11C5 11 1 7 1 2.4z"/></svg>844-GR-WHEEL</li>
      <li><svg viewBox="0 0 12 12"><path d="M3 1h5v3H3zM1 4.5h10V10H1zM3 8h6v3H3z"/></svg>561-278-9053</li>
      <li><svg viewBox="0 0 12 12"><path d="M3 0.5h6v11H3zM4 2v7h4V2z"/></svg>123-456-7890</li>
      <li><svg viewBox="0 0 12 12"><path d="M1 2.5h10v7H1zM1.6 3.2L6 6.6l4.4-3.4z" fill-rule="evenodd"/></svg>info@graniterimsupply-example.com</li>
      <li><svg viewBox="0 0 12 12"><circle cx="6" cy="6" r="5.2"/><path d="M1 6h10M6 1c-2.5 3-2.5 7 0 10M6 1c2.5 3 2.5 7 0 10" stroke="#fff" stroke-width="0.8" fill="none"/></svg>www.graniterimsupply-example.com</li>
    </ul>
  </section>

  <section class="card card-back" aria-label="Card back">
    <h3 class="section-title services-title">SPECIALTY SERVICES</h3>
    <ul class="bullet-list services-list">
      <li>Foam Filling Tires</li>
      <li>Largest Tire Press in SE</li>
      <li>ONSITE Forklift Tire Press</li>
      <li>Boom Truck Services</li>
      <li>Rubber Tracks</li>
    </ul>
    <h3 class="section-title downtime-title">ELIMINATING DOWNTIME</h3>
    <p class="downtime-text">Wheel Exchange Program for New<br>&amp; Used Foam Filled and Solid<br>Rubber Tires</p>
    <h3 class="section-title specialize-title">SPECIALIZING IN NEW AND<br>USED TIRES &amp; WHEELS FOR:</h3>
    <ul class="bullet-list equipment-list">
      <li>Loaders</li>
      <li>Skid Steers</li>
      <li>TelehandlersBoom Lifts</li>
      <li>Forklifs and more</li>
    </ul>
  </section>
</body>
</html>
```